Hardcore nerd needs to stand out in a sea of dull Defence business cards

Wombarra Devices is a new Australian consulting engineering company that turns research and theory into practical systems. No evangelistic fluff, just mathematics and physics into electronic and optical circuits for consumer products, scientific research or Defence applications.

We already have a recognised logo (provided) which is often dark blue/black on a light background but we're open to other combinations. (Us engineers tend to have limited aesthetic imagination :)

Some of our recent products have included:
* Instrumentation for electrical testing,
* Radar jammers,
* GPS antenna design,
* Satellite tracking systems,
* High power lasers

We're open to both single and double-sided designs - happy to be convinced either way.

P.S. Another group is working on the web page, so - alas - our web site is currently of no use for images/ideas...

Target Market(s)

Engineering managers,
Scientists

Contact Information for Business Card

Dr Colin Harte
R&D Engineer

colin@wombarradevices.com.au
0427 563 710

PO Box XXX (to be confirmed)
Kelsby ACT 2917
Australia

Font styles to use
Serif
Sans Serif

Colors

Designer to choose colors to be used in the design.

Requirements
Must have
• My contact details!
• I've had many (great) "bold and plain" designs submitted already, so feel free to be artistically creative :)
• Happy to take advice re fonts/colours/printability etc.
Nice to have
• I'm not sure if "lists" are more at home on a CV than a business card, but representative services include:
• Applied electromagnetics
• RF and high speed electronics
• Signal and image processing
• Electro-optical and laser systems
• Concept-to-prototype design services
• If you're considering double sided cards, then often measuring/alignment grids/rulers feature on the back of similar cards.
• e.g. https://www.veltranoptics.example/newgrouppage9.cfm?objectgroup_id=4183
• https://www.veltranoptics.example/newgrouppage9.cfm?objectgroup_ID=4185
• ..or even a "Smith chart" (google will return lots)
• Generic images to represent a capability might work - googling images associated with keyword for each of these areas might help:
• - "passive radar", "phased array", "fdtd", "vircator"
• RF and high speed electronic design
• - "smith chart", "microstrip circuits", "dimensioned drawing", "electronic schematic"
• - "dft", "iir filter"
• - "optical cavity". "laser energy level diagram"
• Background/watermarked images outlines/wireframes/schematics would probably look OK.
Should not have
• If a list of projects/services is provided, it is important not to make the client feel that this is "all" the company can do. Engineering design is a creative discipline (like graphics :)
• Please, no stock "military" snaps like planes, missiles, etc!

```html
<!DOCTYPE html>
<html lang="en">
<head>
<meta charset="utf-8">
<title>Wombarra Devices – Business Card</title>
<link rel="stylesheet" href="https://fonts.googleapis.com/css2?family=Open+Sans:wght@700&family=Roboto+Condensed:wght@400;700&display=swap">
<style>
  :root {
    --brand-blue: #0d2a7c;
    --paper: #ffffff;
    --muted-grey: #6f6f6f;
    --stage: #3d3d3d;
    --wordmark-font: "Open Sans", Arial, sans-serif;
    --body-font: "Roboto Condensed", "Arial Narrow", sans-serif;
  }
  * { box-sizing: border-box; margin: 0; padding: 0; }
  html, body {
    width: 1200px;
    height: 900px;
    overflow: hidden;
    background: var(--stage);
  }
  .sheet {
    width: 1200px;
    height: 900px;
    display: flex;
    align-items: center;
    justify-content: center;
    gap: 40px;
  }
  .card {
    position: relative;
    width: 540px;
    height: 330px;
    overflow: hidden;
    box-shadow: 0 10px 30px rgba(0,0,0,0.35);
  }

  /* ---------- Front ---------- */
  .card--front { background: var(--paper); }
  .front-shapes {
    position: absolute;
    inset: 0;
  }
  .wordmark {
    position: absolute;
    left: 30px;
    top: 26px;
    font-family: var(--wordmark-font);
    font-weight: 700;
    font-size: 24px;
    letter-spacing: 0.5px;
    color: var(--brand-blue);
    text-transform: uppercase;
  }
  .services {
    position: absolute;
    left: 30px;
    top: 70px;
    font-family: var(--body-font);
    font-size: 13px;
    line-height: 1.3;
    color: var(--brand-blue);
  }
  .person {
    position: absolute;
    right: 26px;
    top: 160px;
    text-align: right;
    font-family: var(--body-font);
  }
  .person__name {
    font-weight: 700;
    font-size: 22px;
    color: var(--brand-blue);
    text-transform: uppercase;
    letter-spacing: 0.3px;
  }
  .person__role {
    font-size: 13px;
    color: var(--muted-grey);
  }
  .contact {
    position: absolute;
    left: 30px;
    top: 196px;
    font-family: var(--body-font);
    font-size: 13px;
    line-height: 1.35;
    color: var(--paper);
    list-style: none;
  }
  .contact li { display: flex; align-items: center; gap: 6px; }
  .contact__address { margin-bottom: 4px; }
  .contact .icon { width: 10px; height: 10px; flex: none; }

  /* ---------- Back ---------- */
  .card--back {
    background: var(--brand-blue);
    display: flex;
    align-items: center;
    justify-content: center;
    gap: 14px;
  }
  .brand-dot {
    width: 54px;
    height: 54px;
    border-radius: 50%;
    background: var(--paper);
  }
  .wordmark--reversed {
    position: static;
    color: var(--paper);
    font-size: 26px;
  }
</style>
</head>
<body>
<main class="sheet">

  <section class="card card--front" aria-label="Business card front">
    <svg class="front-shapes" width="540" height="330" viewBox="0 0 540 330" aria-hidden="true">
      <polygon points="0,150 345,212 345,330 0,330" fill="var(--brand-blue)"/>
      <circle cx="440" cy="268" r="58" fill="none" stroke="var(--brand-blue)" stroke-width="22"/>
    </svg>

    <div class="wordmark">Wombarra Devices</div>

    <p class="services">
      Instrumentation for electrical testing, | Radar jammers,<br>
      GPS antenna design, | Satellite tracking systems, | High power lasers
    </p>

    <div class="person">
      <div class="person__name">Dr Colin Harte</div>
      <div class="person__role">R&amp;D Engineer</div>
    </div>

    <ul class="contact">
      <li class="contact__address">PO Box XXX (to be confirmed)<br>Kelsby ACT 2917 Australia</li>
      <li>
        <svg class="icon" viewBox="0 0 10 10" aria-hidden="true"><path d="M2 0.5 L4 2.5 L3 4 Q4.5 6 6 7 L7.5 6 L9.5 8 L8 9.5 Q3 9 0.5 2 Z" fill="currentColor"/></svg>
        0427 563 710
      </li>
      <li>
        <svg class="icon" viewBox="0 0 10 10" aria-hidden="true"><rect x="0.5" y="2" width="9" height="6" fill="none" stroke="currentColor"/><path d="M0.5 2 L5 5.5 L9.5 2" fill="none" stroke="currentColor"/></svg>
        colin@wombarradevices.com.au
      </li>
      <li>
        <svg class="icon" viewBox="0 0 10 10" aria-hidden="true"><circle cx="5" cy="5" r="4.5" fill="currentColor"/></svg>
        www.wombarradevices.com.au
      </li>
    </ul>
  </section>

  <section class="card card--back" aria-label="Business card back">
    <span class="brand-dot" aria-hidden="true"></span>
    <div class="wordmark wordmark--reversed">Wombarra Devices</div>
  </section>

</main>
</body>
</html>
```